Stylish Business Cards Wanted

- DOUBLE SIDED Design Required -

High end, edgy cards for a corporate and personal stylist. Must include logo,
Name: Belinda Harwick
Title: Director and Stylist
telephone : +61 8 7142 5809
email: belinda@theloombriefing.example
website: theloombriefing.example
Tag: Corporate Workwear & Uniform Specialist | Personal Stylist
Would like nice icons for telephone, email, website

Target Market(s)

Businesses wanting stylish uniforms, people wanting stylish wardrobes

Industry/Entity Type

Corporate Workwear Stylist

Contact Information for Business Card

I would like black, white and gold foiling incorporated in the design - possibly a touch of the other colours on my branding guide attached Name: Belinda Harwick Title: Director and Stylist telephone : +61 8 7142 5809 email: belinda@theloombriefing.example website: theloombriefing.example Tag: Corporate Workwear & Uniform Specialist | Personal Stylist Would like nice icons for telephone, email, website

Font styles to use
Other font styles liked:
• Raleway

Colors

Designer to choose colors to be used in the design.

Requirements
Must have
• Gold foil accents

```html
<!DOCTYPE html>
<html lang="en">
<head>
<meta charset="utf-8">
<title>The Loom Briefing — Business Cards</title>
<link href="https://fonts.googleapis.com/css2?family=Raleway:wght@400;500;700&display=swap" rel="stylesheet">
<style>
  :root {
    --stage: #2a2d31;
    --card: #1f1f20;
    --card-edge: #141414;
    --gold: #e3b23c;
    --white: #f4f4f4;
    --grey: #c9c9c9;
    --silver: #b9b9bb;
  }
  * { box-sizing: border-box; margin: 0; padding: 0; }
  html, body {
    width: 1200px; height: 900px; overflow: hidden;
    background: var(--stage);
    font-family: "Raleway", sans-serif;
  }
  .sheet {
    width: 1200px; height: 900px;
    display: flex; flex-direction: column;
    align-items: center; justify-content: center; gap: 44px;
  }
  .card {
    position: relative;
    width: 660px; height: 385px;
    background: var(--card);
    border-radius: 26px;
    box-shadow: 0 3px 0 var(--card-edge), 0 14px 30px rgba(0,0,0,.45);
    overflow: hidden;
  }

  /* Front */
  .contact {
    position: absolute; left: 56px; top: 92px;
  }
  .contact__name {
    position: relative;
    font-weight: 700; font-size: 27px; letter-spacing: .5px;
    color: var(--gold); text-transform: uppercase;
  }
  .contact__name::before {
    content: ""; position: absolute; left: -22px; top: -2px;
    width: 7px; height: 34px; background: var(--gold);
  }
  .contact__title {
    margin-top: 6px; font-size: 17px; font-weight: 500; color: var(--grey);
  }
  .contact__list { list-style: none; margin-top: 18px; }
  .contact__item {
    display: flex; align-items: center; gap: 10px;
    font-size: 17px; color: var(--white); margin-bottom: 9px;
  }
  .contact__icon { width: 15px; height: 15px; flex: none; }

  .brand {
    position: absolute; display: flex; align-items: center; gap: 12px;
    font-weight: 700; text-transform: uppercase; letter-spacing: 3px;
  }
  .brand__mark { width: 14px; height: 14px; }
  .brand--front { right: 50px; bottom: 90px; font-size: 30px; color: var(--white); }
  .brand--front .brand__mark { background: var(--gold); }

  /* Back */
  .brand--back {
    left: 50%; top: 40%; transform: translate(-50%, -50%);
    font-size: 36px; color: var(--silver);
  }
  .brand--back .brand__mark { background: var(--silver); }
  .tagline {
    position: absolute; left: 0; right: 0; bottom: 48px;
    text-align: center; font-size: 15px; font-weight: 500;
    letter-spacing: 1px; color: var(--gold); text-transform: uppercase;
  }
</style>
</head>
<body>
<main class="sheet">

  <section class="card card--front" aria-label="Card front">
    <div class="contact">
      <h1 class="contact__name">Belinda Harwick</h1>
      <p class="contact__title">Director and Stylist</p>
      <ul class="contact__list">
        <li class="contact__item">
          <svg class="contact__icon" viewBox="0 0 16 16"><path fill="#e3b23c" d="M3.6 1.2l2.3 2.3-1.4 2a9 9 0 0 0 6 6l2-1.4 2.3 2.3-1.6 2.2C7.4 15 1 8.6 1.4 2.8z"/></svg>
          <span>+61 8 7142 5809</span>
        </li>
        <li class="contact__item">
          <svg class="contact__icon" viewBox="0 0 16 16"><rect x="1" y="3" width="14" height="10" rx="1" fill="#e3b23c"/><path d="M1.5 3.8L8 9l6.5-5.2" stroke="#1f1f20" stroke-width="1.4" fill="none"/></svg>
          <span>belinda@theloombriefing.example</span>
        </li>
        <li class="contact__item">
          <svg class="contact__icon" viewBox="0 0 16 16"><circle cx="8" cy="8" r="6.6" fill="none" stroke="#e3b23c" stroke-width="1.6"/><ellipse cx="8" cy="8" rx="2.8" ry="6.6" fill="none" stroke="#e3b23c" stroke-width="1.3"/><path d="M1.6 8h12.8" stroke="#e3b23c" stroke-width="1.3"/></svg>
          <span>www.theloombriefing.example</span>
        </li>
      </ul>
    </div>
    <div class="brand brand--front"><span class="brand__mark"></span><span>The Loom Briefing</span></div>
  </section>

  <section class="card card--back" aria-label="Card back">
    <div class="brand brand--back"><span class="brand__mark"></span><span>The Loom Briefing</span></div>
    <p class="tagline">Corporate Workwear | Uniform Specialist | Personal Stylist</p>
  </section>

</main>
</body>
</html>
```